Harbor Crest Holdings Corporate Showcase

Provide an attractive Corporate Website for a boutique Investment Company to showcase our activities and corporate interests.

Our Company works across a number of Sectors including

Real Estate
E-Commerce
Healthcare
Beauty & Personal Care
Technology
Resources

Lets keep the personality

Modern
Global
Sophisticated
Calm
Interesting

Lets keep the pages with MINIMAL Words
Lets use Photos/ Imagery to tell the story

We'll need a Banner Menu -
About Us
Expertise
Global Outlook
Sectors
Management
Media
Contact Us

Many thanks
Best wishes
Dennis.

Target Market(s)

Investors
Clients

Coding

Coded - Design and coding required

Number of Pages Required

5+ page

Font styles to use
Sans Serif

Colors
886aae
3176b5
00a990
f68e4d
f04a50
e667a6

Requirements
Must have
• WordPress Coding

Checkout this Website for look and feel - its cool:
www.qvr-example.com

Harbor Crest Partners
(Harbor Crest Holdings LLP)
London
E9 4ZX
United Kingdom

www.HarborCrestPartners-example.com
Nice to have
• Sophisticated colour palette - black/ brown/ blue/ purple/

```html
<!DOCTYPE html>
<html lang="en">
<head>
<meta charset="utf-8">
<title>Harbor Crest Holdings</title>
<link href="https://fonts.googleapis.com/css2?family=Oswald:wght@400;500&family=Roboto:wght@400;500&family=Montserrat:wght@400;500&display=swap" rel="stylesheet">
<style>
:root{
  --orange:#f68e4d;
  --red:#e8473f;
  --blue:#3176b5;
  --ink:#111111;
  --text:#555555;
  --muted:#8a8a8a;
  --panel:#f6f6f6;
  --line:#d9d9d9;
  --footer:#0d0d0d;
  --white:#ffffff;
}
*{box-sizing:border-box;margin:0;padding:0}
html,body{width:1200px;height:4183px;overflow:hidden;background:var(--white)}
body{position:relative;font-family:'Roboto',Arial,sans-serif;color:var(--ink)}
.abs{position:absolute}
.heading{font-family:'Oswald',Arial Narrow,sans-serif;font-weight:500;text-transform:uppercase;color:var(--ink);font-size:54px;line-height:1}
.center{left:0;width:1200px;text-align:center}
.rule{position:absolute;height:3px;width:41px;background:var(--red)}
.btn{position:absolute;background:var(--orange);color:var(--white);font-family:'Roboto',Arial,sans-serif;font-weight:500;font-size:13px;text-transform:uppercase;display:flex;align-items:center;justify-content:center}
.copy{font-family:'Roboto',Arial,sans-serif;font-size:12px;line-height:26.5px;color:var(--text)}

/* header */
.logo{font-family:'Oswald',Arial Narrow,sans-serif;font-weight:500;color:var(--blue);text-align:center;line-height:1.1;font-size:28px}
.nav{position:absolute;top:66px;left:425px;display:flex;gap:18px;font-size:15px;color:var(--ink)}
.nav .active{color:var(--orange)}
.circle{position:absolute;border-radius:50%;border:1.5px solid #4a78b8}

/* hero */
.hero{position:absolute;left:0;top:102px;width:1200px;height:600px;background:linear-gradient(100deg,#3f5e86 0%,#6f8fb3 35%,#9fb6cc 60%,#5d7898 100%)}
.hero-title{left:110px;top:152px;font-family:'Oswald',sans-serif;font-weight:500;font-size:62px;line-height:62px;color:var(--white);text-transform:uppercase}
.hero-sub{left:110px;top:290px;font-family:'Oswald',sans-serif;font-size:25px;color:var(--white)}
.dot{position:absolute;width:10px;height:10px;border-radius:50%;background:rgba(255,255,255,.5)}

/* sector cards */
.card{position:absolute;top:880px;width:318px;height:440px;background:var(--white);box-shadow:0 2px 10px rgba(0,0,0,.15);text-align:center}
.card .photo{height:227px}
.card h3{font-family:'Roboto',sans-serif;font-weight:500;font-size:22px;margin-top:24px}
.card p{font-size:13px;line-height:26.5px;color:var(--text);margin:8px 18px 0}
.card .btn{left:93px;top:382px;width:131px;height:40px}

/* media */
.mcard{position:absolute;background:var(--white);box-shadow:0 2px 10px rgba(0,0,0,.14);font-family:'Montserrat',sans-serif}
.mcard h4{font-weight:500;font-size:17px;line-height:25px;color:var(--ink)}
.mcard p{font-size:12px;line-height:23px;color:var(--muted);margin-top:6px}
.more{color:var(--orange);font-size:15px;font-weight:500;display:flex;align-items:center;gap:10px;margin-top:14px}

/* form */
.field{position:absolute;border:1.5px solid var(--line);font-family:'Montserrat',sans-serif;font-size:13px;color:var(--muted);padding-left:18px;display:flex;align-items:center;gap:6px;background:var(--white)}

/* footer */
.footer{position:absolute;left:0;top:3849px;width:1200px;height:334px;background:var(--footer);color:var(--white)}
.fnav{position:absolute;top:92px;left:416px;display:flex;gap:15px;font-size:15px}
.fhead{position:absolute;top:168px;font-weight:500;font-size:16px;display:flex;align-items:center;gap:8px}
.ftext{position:absolute;top:198px;font-size:13.5px;line-height:28px}
.vline{position:absolute;top:154px;width:1px;height:97px;background:#333}
.fcircle{position:absolute;top:207px;width:26px;height:26px;border:1.5px solid var(--white);border-radius:50%}
</style>
</head>
<body>

<!-- header -->
<header>
  <div class="abs logo" style="left:100px;top:18px;width:280px">HARBOR CREST<br>HOLDINGS</div>
  <svg class="abs" style="left:796px;top:8px" width="36" height="36" viewBox="0 0 36 36"><circle cx="18" cy="18" r="18" fill="#3f6fb0"/><path d="M12 10c1-1 2-1 3 0l2 3c.5 1 0 2-1 2.5l-1 .6c.8 2 2.5 3.8 4.5 4.6l.7-1c.6-.9 1.5-1.2 2.4-.7l3 2c1 .7 1 1.8 0 2.7-1.4 1.4-3 2-5 1.3-4.5-1.6-8.1-5.2-9.7-9.7-.6-1.8 0-3.5 1.1-5.3z" fill="#fff"/></svg>
  <div class="abs" style="left:841px;top:15px;font-size:17px;color:#444">555-010-2040</div>
  <span class="circle" style="left:983px;top:12px;width:28px;height:28px"></span>
  <span class="circle" style="left:1020px;top:12px;width:28px;height:28px"></span>
  <span class="circle" style="left:1057px;top:12px;width:28px;height:28px"></span>
  <nav class="nav">
    <span class="active">Home</span><span>About Us</span><span>Expertise</span><span>Global Outlook</span><span>Sectors</span><span>Management</span><span>Media</span><span>Contact Us</span>
  </nav>
</header>

<!-- hero -->
<section class="hero" role="img" aria-label="Photo of a business team meeting around a table in a glass office">
  <div class="abs hero-title">Harbor Crest<br>Holdings.</div>
  <div class="abs hero-sub">Growing the Next Generation Of Business</div>
  <div class="btn" style="left:114px;top:351px;width:167px;height:49px;font-weight:400;font-size:17px">Get Started</div>
  <svg class="abs" style="left:56px;top:285px" width="30" height="30"><circle cx="15" cy="15" r="13" fill="none" stroke="rgba(255,255,255,.5)" stroke-width="1.5"/><path d="M17 9l-6 6 6 6" fill="none" stroke="rgba(255,255,255,.7)" stroke-width="1.5"/></svg>
  <svg class="abs" style="left:1108px;top:285px" width="30" height="30"><circle cx="15" cy="15" r="13" fill="none" stroke="rgba(255,255,255,.5)" stroke-width="1.5"/><path d="M13 9l6 6-6 6" fill="none" stroke="rgba(255,255,255,.7)" stroke-width="1.5"/></svg>
  <span class="dot" style="left:562px;top:559px;background:#fff"></span>
  <span class="dot" style="left:585px;top:559px"></span>
  <span class="dot" style="left:623px;top:559px"></span>
</section>

<!-- sectors -->
<section>
  <h2 class="abs heading center" style="top:780px">Our Sectors</h2>
  <span class="rule" style="left:581px;top:842px"></span>
  <svg class="abs" style="left:56px;top:1074px" width="16" height="26"><path d="M12 2L3 13l9 11" fill="none" stroke="#999" stroke-width="1.5"/></svg>
  <svg class="abs" style="left:1130px;top:1074px" width="16" height="26"><path d="M4 2l9 11-9 11" fill="none" stroke="#999" stroke-width="1.5"/></svg>
  <article class="card" style="left:101px">
    <div class="photo" role="img" aria-label="Photo of a handshake over a small house model" style="background:linear-gradient(135deg,#3b3f4a,#8a7b6c 55%,#d9d2c6)"></div>
    <h3>Real Estate</h3>
    <p>Lorem ipsum dolor sit amet, consectur adipis lit, sed do eiusmod tempor incididunt ut labore et dolore magna aliqua.</p>
    <div class="btn">Learn More</div>
  </article>
  <article class="card" style="left:442px">
    <div class="photo" role="img" aria-label="Photo of small shopping parcels on a laptop keyboard" style="background:linear-gradient(135deg,#e9c97a,#d9a070 55%,#9a8a6a)"></div>
    <h3>E-Commerce</h3>
    <p>Lorem ipsum dolor sit amet, consectur adipis lit, sed do eiusmod tempor incididunt ut labore et dolore magna aliqua.</p>
    <div class="btn">Learn More</div>
  </article>
  <article class="card" style="left:781px">
    <div class="photo" role="img" aria-label="Photo of a medical professional with digital health graphics" style="background:linear-gradient(135deg,#0e3f7c,#2a7fc7 55%,#8fc3ea)"></div>
    <h3>Healthcare</h3>
    <p>Lorem ipsum dolor sit amet, consectur adipis lit, sed do eiusmod tempor incididunt ut labore et dolore magna aliqua.</p>
    <div class="btn">Learn More</div>
  </article>
</section>

<!-- about -->
<section>
  <div class="abs" style="left:0;top:1444px;width:601px;height:458px;background:var(--panel)"></div>
  <div class="abs" role="img" aria-label="Photo of a businessman climbing stairs toward a city skyline" style="left:601px;top:1444px;width:599px;height:458px;background:linear-gradient(180deg,#e8b26a 0%,#b9a998 35%,#6d7682 70%,#4a525c 100%)"></div>
  <h2 class="abs heading" style="left:117px;top:1528px">About Us</h2>
  <span class="rule" style="left:117px;top:1595px;width:38px"></span>
  <p class="abs copy" style="left:110px;top:1616px;width:425px">Lorem ipsum dolor sit amet, consectetur adipiscing elit, o eiusmod tempor incididunt ut labore et dolore magna aliqua. Quis ipsendisse trices gravida. Risus commodo viverra maecenas accumsan lus vel facilisis. Lorem ipsum dolor sit amet, consectetur adipiscing elit, o eiusmod tempor incididunt ut labore et dolore magna aliqua. Quis ipsendisse ultrices gravida.</p>
  <div class="btn" style="left:110px;top:1777px;width:134px;height:42px">Learn More</div>
</section>

<!-- media -->
<section>
  <h2 class="abs heading center" style="top:1988px">Media</h2>
  <span class="rule" style="left:580px;top:2051px"></span>

  <article class="mcard" style="left:122px;top:2092px;width:466px;height:576px">
    <div role="img" aria-label="Photo of a desk with laptop, calculator and financial charts" style="height:355px;background:linear-gradient(135deg,#5b6677,#aab4c0 50%,#e4e7ec)"></div>
    <div style="padding:26px 20px 0">
      <h4 style="font-size:19.5px;line-height:28px">Lorem ipsum dolor sit amet, adipiscing elit, sed do eiusmod tempor</h4>
      <p style="font-size:12.5px;line-height:26px;margin-top:10px">Lorem ipsum dolor sit amet, consectetur adipiscing elit, sed do eiusmod tempor incididunt ut labore et dolore magna aliqua. Quis ipsum suspendisse ultrices gravida.</p>
      <div class="more">Read More <svg width="16" height="10"><path d="M0 5h13M9 1l4 4-4 4" fill="none" stroke="#f68e4d" stroke-width="2"/></svg></div>
    </div>
  </article>

  <article class="mcard" style="left:612px;top:2092px;width:466px;height:177px">
    <div style="position:absolute;left:21px;top:20px;width:290px">
      <h4>Lorem ipsum dolor sit amet, consectetur adipiscing</h4>
      <p>Lorem ipsum dolor sit amet, consectetur adipiscing elit, sed do eiusmod</p>
      <div class="more">Read More <svg width="16" height="10"><path d="M0 5h13M9 1l4 4-4 4" fill="none" stroke="#f68e4d" stroke-width="2"/></svg></div>
    </div>
    <div role="img" aria-label="Photo of a hand placing a coin on stacks of coins" style="position:absolute;right:0;top:0;width:150px;height:177px;background:linear-gradient(135deg,#f2efe9,#c9a878 60%,#8b6a45)"></div>
  </article>

  <article class="mcard" style="left:612px;top:2291px;width:466px;height:178px">
    <div role="img" aria-label="Photo of a man and a girl looking at a laptop together" style="position:absolute;left:0;top:0;width:150px;height:178px;background:linear-gradient(135deg,#7a9cb0,#c9b39a 60%,#e9ddd0)"></div>
    <div style="position:absolute;left:176px;top:20px;width:280px">
      <h4>Lorem ipsum dolor sit amet, consectetur adipiscing</h4>
      <p>Lorem ipsum dolor sit amet, consectetur adipiscing elit, sed do eiusmod</p>
      <div class="more">Read More <svg width="16" height="10"><path d="M0 5h13M9 1l4 4-4 4" fill="none" stroke="#f68e4d" stroke-width="2"/></svg></div>
    </div>
  </article>

  <article class="mcard" style="left:612px;top:2491px;width:466px;height:177px">
    <div style="position:absolute;left:24px;top:20px;width:290px">
      <h4>Lorem ipsum dolor sit amet, consectetur adipiscing</h4>
      <p>Lorem ipsum dolor sit amet, consecte-tur adipiscing elit, sed do eiusmod</p>
      <div class="more">Read More <svg width="16" height="10"><path d="M0 5h13M9 1l4 4-4 4" fill="none" stroke="#f68e4d" stroke-width="2"/></svg></div>
    </div>
    <div role="img" aria-label="Image of a rising arrow over a blue financial chart" style="position:absolute;right:0;top:0;width:150px;height:177px;background:linear-gradient(135deg,#bcd4ec,#4f86c2 55%,#1f4f8a)"></div>
  </article>
</section>

<!-- global outlook -->
<section>
  <div class="abs" role="img" aria-label="Image of a businessman holding a glowing growth chart for 2019 to 2021" style="left:0;top:2757px;width:599px;height:458px;background:linear-gradient(120deg,#243247 0%,#3f5877 45%,#1b1f29 100%)"></div>
  <div class="abs" style="left:599px;top:2757px;width:601px;height:458px;background:var(--panel)"></div>
  <h2 class="abs heading" style="left:677px;top:2839px">Global Outlook</h2>
  <span class="rule" style="left:677px;top:2903px;width:38px"></span>
  <p class="abs copy" style="left:671px;top:2930px;width:425px">Lorem ipsum dolor sit amet, consectetur adipiscing elit, o eiusmod tempor incididunt ut labore et dolore magna aliqua. Quis ipsendisse trices gravida. Risus commodo viverra maecenas accumsan lus vel facilisis. Lorem ipsum dolor sit amet, consectetur adipiscing elit, o eiusmod tempor incididunt ut labore et dolore magna aliqua. Quis ipsendisse ultrices gravida.</p>
  <div class="btn" style="left:671px;top:3091px;width:132px;height:41px">Learn More</div>
</section>

<!-- contact -->
<section>
  <h2 class="abs heading center" style="top:3293px">Contact Us</h2>
  <span class="rule" style="left:580px;top:3356px"></span>
  <div class="field" style="left:253px;top:3386px;width:350px;height:48px"><svg width="10" height="10"><circle cx="5" cy="3" r="2.5" fill="#bbb"/><path d="M0 10c0-3 2-4.5 5-4.5s5 1.5 5 4.5z" fill="#bbb"/></svg>First Name</div>
  <div class="field" style="left:610px;top:3386px;width:334px;height:48px"><svg width="10" height="10"><circle cx="5" cy="3" r="2.5" fill="#bbb"/><path d="M0 10c0-3 2-4.5 5-4.5s5 1.5 5 4.5z" fill="#bbb"/></svg>Last Name</div>
  <div class="field" style="left:253px;top:3446px;width:691px;height:48px"><svg width="10" height="10"><path d="M2 1l2 2-1 1.5c.7 1.3 1.5 2 2.5 2.5L7 6l2 2-1.5 1.5C5 9.5 1 5.5.5 2.5z" fill="#bbb"/></svg>Your phone</div>
  <div class="field" style="left:253px;top:3506px;width:691px;height:48px"><svg width="11" height="9"><rect x=".5" y=".5" width="10" height="8" fill="none" stroke="#bbb"/></svg>Your Email</div>
  <div class="field" style="left:253px;top:3566px;width:691px;height:128px;align-items:flex-start;padding-top:16px"><svg width="11" height="10"><ellipse cx="5.5" cy="4.5" rx="5" ry="3.8" fill="#bbb"/></svg>How Can we help you?</div>
  <div class="btn" style="left:447px;top:3714px;width:307px;height:48px;font-size:15px;gap:8px">Submit <svg width="14" height="14"><path d="M1 7L13 1 10 13 7 9z" fill="#fff"/></svg></div>
</section>

<!-- footer -->
<footer class="footer">
  <div class="abs logo" style="left:95px;top:48px;width:280px;color:var(--white)">HARBOR CREST<br>HOLDINGS</div>
  <nav class="fnav"><span>Home</span><span>About Us</span><span>Expertise</span><span>Global Outlook</span><span>Sectors</span><span>Management</span><span>Media</span><span>Contact Us</span></nav>

  <div class="fhead" style="left:110px"><svg width="12" height="16"><path d="M6 0a6 6 0 0 0-6 6c0 4.5 6 10 6 10s6-5.5 6-10a6 6 0 0 0-6-6z" fill="#fff"/><circle cx="6" cy="6" r="2.3" fill="#0d0d0d"/></svg>ADDRESS</div>
  <div class="ftext" style="left:112px">48 Quayside Row, Harborview<br>20418, United States</div>
  <span class="vline" style="left:349px"></span>

  <div class="fhead" style="left:403px"><svg width="12" height="16"><path d="M6 0a6 6 0 0 0-6 6c0 4.5 6 10 6 10s6-5.5 6-10a6 6 0 0 0-6-6z" fill="#fff"/><circle cx="6" cy="6" r="2.3" fill="#0d0d0d"/></svg>PHONE</div>
  <div class="ftext" style="left:404px">(555) 010 2040</div>
  <span class="vline" style="left:557px"></span>

  <div class="fhead" style="left:610px"><svg width="12" height="16"><path d="M6 0a6 6 0 0 0-6 6c0 4.5 6 10 6 10s6-5.5 6-10a6 6 0 0 0-6-6z" fill="#fff"/><circle cx="6" cy="6" r="2.3" fill="#0d0d0d"/></svg>EMAIL</div>
  <div class="ftext" style="left:611px">info@harborcrestholdings-example.com</div>
  <span class="vline" style="left:890px"></span>

  <div class="fhead" style="left:944px"><svg width="12" height="16"><path d="M6 0a6 6 0 0 0-6 6c0 4.5 6 10 6 10s6-5.5 6-10a6 6 0 0 0-6-6z" fill="#fff"/><circle cx="6" cy="6" r="2.3" fill="#0d0d0d"/></svg>SOCIAL MEDIA</div>
  <span class="fcircle" style="left:946px"></span>
  <span class="fcircle" style="left:979px"></span>
  <span class="fcircle" style="left:1011px"></span>
  <span class="fcircle" style="left:1044px"></span>

  <div class="abs" style="left:110px;top:271px;width:978px;height:1px;background:#333"></div>
  <div class="abs" style="left:110px;top:296px;font-size:12.5px">Copyright © 2020 Harbor Crest Holdings. All Rights Reserved.</div>
  <div class="abs" style="right:112px;top:296px;font-size:12.5px">Terms and Conditions &nbsp;|&nbsp; Privacy Policy</div>
</footer>

</body>
</html>
```